July 2022 Industrial Manufacturer Product Expo Mexico City

We manufacture large screws and fastners for large Mining equipment, Trains, large ships, airplanes, wind turbines, and so on. We also do custom work base on the customer needs. No matter the size we can make it.
We have a Expo coming up with companies all over the world. We have to stand out we are a family own business so our customer service will be above and beyond anyone can provide. We do not have a sales force to push our products and services we provide one on one service.
Plus@!! I'm looking for anything that you designers can come up with if it was your company to put on a business card, plus i want to do a 1 or 2 sided pamphlet, and then a website. We make Speciality Bolts for large mining equipment these bolts can be 3 to 4 foot long!!! Plus fasteners, Nuts, washers, any, size, strengths, special materials, we offer more of a ono on one customer service, We are a small company, family own, but can fulfill any type of orders. We can also provide special time lines for emergency orders. "We keep the machines running we here at KRV don't believe in down time" We want to hear any slogan based on our company to stand out.
Thanks i really appreciate all your work and options that we have to pick on. Plus just a thought we could possibly want to entertain a experience Marketing internet help maybe a employment possibility. Thanks

I need 2 cards one in Spanish and English Like the steel back ground maybe send me in some bright red and blue writing Same with the Black cards Please remove the word Military The logo KRV maybe integrate a picture of a Bolt 🔩 Thank you

Still looking for I need 2 cards one in Spanish and English Like the steel back ground maybe send me in some bright red and blue writing Same with the Black cards try bright writing Please remove the word Military The logo KRV maybe integrate a picture of a Bolt 🔩 Plus will need the company to make a brochure and website next Thank you

Target Market(s)

Large Mining, Ship, Train, Green Energy, VELM, and Government equipment. Throughout the World

Industry/Entity Type

We can Custom Manufacture any type of Fastners for Mining equipment, Trains, Ships, Green energy, Governments, or military projects. wind turbines,

Contact Information for Business Card

I attached the name and contact info that's on a card, plus the Company Logo. Would like industrial looking background with Bright Colors that will stand out!! If we can insert somewhere maybe on back that we "Custom Manufacture Any Size or Quantity Fastners for Large Mining Equipment, Trains, Ships, Green Energy Equipment or Government Projects

Font styles to use
Other font styles liked:
• You Pick, has to be bold, colorful standout, Professional looking Beable to read it.

Colors

Designer to choose colors to be used in the design.

Requirements
Must have
• Need in Spanish and English TO STANDOUT FROM THE REST OF THE EXPO!! See Business card details, Rounded corners
Nice to have
• Can i see some of the darker cards with Bright Red and Blue letters I like to see the different type of card material, heavy thickness, plastic, transparent, Metal types, Bright Colors, I saw like Raised letters like on the logo.

```html
<!DOCTYPE html>
<html lang="es">
<head>
<meta charset="utf-8">
<title>KRV – Tarjetas de presentación</title>
<link rel="stylesheet" href="https://fonts.googleapis.com/css2?family=Tinos:wght@400;700&display=swap">
<style>
  :root {
    --stage: #b7b7b7;
    --paper: #ffffff;
    --steel-dark: #050505;
    --steel-mid: #2a2a2d;
    --steel-light: #68686d;
    --accent-blue: #1a8fd6;
    --deep-blue: #0b1f8c;
    --band-top: #0a2fb0;
    --band-bottom: #1a8ad8;
    --rule-gray: #7a7a7a;
    --logo-gray: #4a4a4e;
    --logo-silver: #d4d4d4;
    --text-light: #ffffff;
    --shadow: #2b2b2b;
  }
  * { box-sizing: border-box; margin: 0; padding: 0; }
  html, body { width: 1075px; height: 1200px; overflow: hidden; }
  body {
    background: var(--stage);
    font-family: "Tinos", "Times New Roman", serif;
    position: relative;
  }
  .card {
    position: absolute;
    left: 206px;
    width: 663px;
    height: 396px;
    overflow: hidden;
    box-shadow: 4px 4px 0 var(--shadow);
  }
  .card--front { top: 187px; background: var(--paper); }
  .card--back {
    top: 637px;
    background: linear-gradient(200deg, var(--steel-light) 0%, var(--steel-mid) 45%, var(--steel-dark) 100%);
  }

  .wordmark {
    position: absolute;
    font-weight: 700;
    letter-spacing: 6px;
    line-height: 1;
    display: flex;
    align-items: center;
    gap: 14px;
  }
  .wordmark__mark { width: 18px; height: 18px; background: var(--accent-blue); }
  .card--front .wordmark { left: 262px; top: 66px; font-size: 86px; color: var(--logo-gray); }
  .card--back .wordmark { left: 130px; top: 122px; font-size: 86px; color: var(--logo-silver); }

  .holder-name {
    position: absolute;
    left: 35px;
    top: 222px;
    font-size: 23.5px;
    color: var(--accent-blue);
  }
  .holder-rule {
    position: absolute;
    left: 35px;
    top: 264px;
    width: 333px;
    height: 15px;
    background: var(--rule-gray);
  }
  .holder-rule::after {
    content: "";
    position: absolute;
    left: 0; right: 0; top: 5px;
    height: 4px;
    background: var(--deep-blue);
  }

  .contact-band {
    position: absolute;
    left: 0; right: 0; top: 271px; bottom: 0;
    background: linear-gradient(200deg, var(--steel-light) 0%, var(--steel-mid) 50%, var(--steel-dark) 100%);
    color: var(--text-light);
    font-size: 18px;
  }
  .contact-band__email {
    position: absolute;
    left: 35px;
    top: 50px;
    line-height: 25px;
  }
  .contact-band__phones {
    position: absolute;
    right: 40px;
    top: 55px;
    line-height: 24px;
    text-align: right;
    list-style: none;
    letter-spacing: 0.5px;
  }
  .contact-band__phones li { display: flex; align-items: center; justify-content: flex-end; gap: 3px; }
  .contact-band__phones svg { width: 16px; height: 16px; }

  .tagline-band {
    position: absolute;
    left: 0;
    top: 306px;
    width: 660px;
    height: 90px;
    background: linear-gradient(180deg, var(--band-top) 0%, var(--band-bottom) 100%);
    color: var(--text-light);
    font-size: 19.5px;
    line-height: 23.5px;
    text-align: center;
    padding-top: 10px;
  }
</style>
</head>
<body>

<section class="card card--front" aria-label="Frente de la tarjeta">
  <div class="wordmark"><span>KRV</span><span class="wordmark__mark"></span></div>
  <p class="holder-name">Lic.Mariela Fonseca Ruiz</p>
  <div class="holder-rule"></div>
  <div class="contact-band">
    <p class="contact-band__email">Cotizaciones en<br>tornilleriakrv.ventas@correo.mx</p>
    <ul class="contact-band__phones">
      <li>5550193601
        <svg viewBox="0 0 16 16" aria-hidden="true"><path d="M4 1.5l2.2 3-1.3 1.6c.8 1.9 2.1 3.2 4 4l1.6-1.3 3 2.2-1.2 2.6C7 13.3 2.7 9 1.9 2.7z" fill="#fff"/><path d="M9.5 2.5a4 4 0 0 1 4 4M9.5 4.6a2 2 0 0 1 1.9 1.9" stroke="#fff" stroke-width="1.2" fill="none"/></svg>
      </li>
      <li>5550127600
        <svg viewBox="0 0 16 16" aria-hidden="true"><rect x="3.5" y="1" width="9" height="14" rx="1.5" fill="none" stroke="#fff" stroke-width="1.4"/><rect x="7" y="12" width="2" height="1.2" fill="#fff"/></svg>
      </li>
    </ul>
  </div>
</section>

<section class="card card--back" aria-label="Reverso de la tarjeta">
  <div class="wordmark"><span>KRV</span><span class="wordmark__mark"></span></div>
  <p class="tagline-band">Custom Manufacture Any Size or Quantity Fastners for Large<br>Mining Equipment, Trains, Ships, Green Energy Equipment,<br>Military or Government Projects</p>
</section>

</body>
</html>
```